Zielgruppe
Ich biete Menschen, die in ihrem Beruf hohen Stressbelastungen ausgesetzt sind, schnelle und wirksame Hilfe. Sie können bei mir lernen, langfristig ohne Stress in ihrem Job erfolgreich zu sein.
Mein Angebot nennt sich „Mit Ruhe ans Ziel“. Es besteht aus drei Bausteinen, einem wissenschaftlichem Stresstest, intensiven Kleingruppen-Workshops und individuellem Einzelcoaching.
So kann ich flexibel für jeden die passende Lösungsstrategie zur Stressbewältigung anbieten.
Aufgabenstellung
Farbwelt des Logos Mit Ruhe ans Ziel berücksichtigen
Persönlichen Daten/Adressdaten auf der Vorderseite:
Marlene Kaltenbach
Personal/Business Coach
Stressmanagement-Trainerin
Beraterin für KALMA Belastungsvorsorge by Hardorf®
Lindauer Weg 17
10437 Berlin
Tel: (030) 41267385
Mobil: (0173) 8204619
Email: info@mit-ruhe-ans-ziel.de
Text auf der Rückseite:
Mit Ruhe ans Ziel:
Wissenschaftlicher Stresstest KALMA
Intensive Kleingruppen-Workshops
Individuelles Coaching
www.mit-ruhe-ans-ziel.de

```html
<!DOCTYPE html>
<html lang="de">
<head>
<meta charset="utf-8">
<title>Mit Ruhe ans Ziel – Visitenkarten</title>
<link href="https://fonts.googleapis.com/css2?family=Hind:wght@400;500;600;700&display=swap" rel="stylesheet">
<style>
  :root {
    --green: #7cbd3b;
    --pink: #b5587a;
    --ink: #2a2a2a;
    --text: #3c3c3c;
    --paper: #ffffff;
    --bg: #f8f7f5;
  }
  * { box-sizing: border-box; margin: 0; padding: 0; }
  html, body { width: 842px; height: 1200px; overflow: hidden; }
  body {
    background: var(--bg);
    font-family: "Hind", Arial, sans-serif;
    color: var(--text);
    position: relative;
  }
  .brand {
    display: flex; align-items: center; gap: 7px;
    color: var(--green); font-weight: 600; white-space: nowrap;
  }
  .brand-dot { border-radius: 50%; background: var(--pink); flex: none; }
  .brand--hero {
    position: absolute; left: 0; right: 0; top: 88px;
    justify-content: center; font-size: 32px;
  }
  .brand--hero .brand-dot { width: 11px; height: 11px; }
  .brand--card { position: absolute; left: 62px; top: 30px; font-size: 22px; }
  .brand--card .brand-dot { width: 8px; height: 8px; }

  .card {
    position: absolute; top: 231px; width: 371px; height: 239px;
    background: var(--paper);
    box-shadow: 6px 10px 16px rgba(0,0,0,.14);
  }
  .card--front { left: 36px; border-left: 4px solid var(--green); }
  .card--back { left: 435px; }

  .holder { position: absolute; left: 57px; top: 89px; font-size: 10.5px; font-weight: 600; color: var(--ink); }
  .services { list-style: none; position: absolute; font-size: 10px; line-height: 14.7px; }
  .services li { display: flex; align-items: center; }
  .services li::before {
    content: ""; width: 4px; height: 4px; border-radius: 50%;
    background: var(--pink); margin-right: 5px; flex: none;
  }
  .card--front .services { left: 57px; top: 108px; }
  .card--back .services { left: 93px; top: 109px; }

  .address { position: absolute; left: 42px; top: 194px; font-size: 9.6px; line-height: 14px; font-style: normal; }
  .divider { position: absolute; left: 174px; top: 177px; width: 1.4px; height: 62px; background: var(--pink); }
  .contact { list-style: none; position: absolute; left: 187px; top: 180px; font-size: 9.6px; line-height: 14px; }
  .contact li { display: flex; align-items: center; gap: 5px; }
  .contact svg { width: 9px; height: 9px; fill: var(--pink); flex: none; }

  .web { position: absolute; left: 84px; top: 204px; font-size: 12.5px; font-weight: 700; color: var(--green); }
</style>
</head>
<body>
  <div class="brand brand--hero"><span class="brand-dot"></span>Mit Ruhe ans Ziel</div>

  <section class="card card--front" aria-label="Vorderseite">
    <div class="brand brand--card"><span class="brand-dot"></span>Mit Ruhe ans Ziel</div>
    <p class="holder">Marlene Kaltenbach</p>
    <ul class="services">
      <li>Personal/Business Coach</li>
      <li>Stressmanagement-Trainerin</li>
      <li>Beraterin für KALMA Belastungsvorsorge by Hardorf®</li>
    </ul>
    <address class="address">Lindauer Weg 17<br>10437 Berlin</address>
    <div class="divider"></div>
    <ul class="contact">
      <li><svg viewBox="0 0 10 10"><path d="M2 0.5 3.6 2.6 2.6 3.6C3.2 5 4.8 6.6 6.3 7.3L7.3 6.3 9.5 7.9 8.4 9.5C4.5 9.3 0.7 5.5 0.5 1.6Z"/></svg>(030) 41267385</li>
      <li><svg viewBox="0 0 10 10"><path d="M2.5 0h5v10h-5zM3.3 1v7h3.4V1z"/></svg>(0173) 8204619</li>
      <li><svg viewBox="0 0 10 10"><path d="M0 1.5h10v7H0zM1 2.3 5 5.4 9 2.3z"/></svg>info@mit-ruhe-ans-ziel.de</li>
    </ul>
  </section>

  <section class="card card--back" aria-label="Rückseite">
    <div class="brand brand--card"><span class="brand-dot"></span>Mit Ruhe ans Ziel</div>
    <ul class="services">
      <li>Wissenschaftlicher Stresstest KALMA</li>
      <li>Intensive Kleingruppen-Workshops</li>
      <li>Individuelles Coaching</li>
    </ul>
    <p class="web">www.mit-ruhe-ans-ziel.de</p>
  </section>
</body>
</html>
```